Interior Design & Furniture E commerce Website Design

I need a cutting edge website design, this is for Interior Design Services as well as eCommerce for furniture and home decor www.lorivexstudio.com
Here is a sample of the concept behind the site.
I am a furniture & Interior Designer, want to create a life style brand.
Will offer Interior Design Services : Commercial & Residential (this portion will be a catalog or portfolio type)
The eCommerce side will sell, Furniture, Lighting, Decor, Gifts, Textiles, will also be offering trade so that could be at bottom of site. I also like the concept of concierge as where all the info falls under: shipping, etc..

*Please make sure to make the eCommerce prominent.

Gathering more feedback

Hello Designers, I also would like to possibly update my logo, the current one I like but don't Love.

Target Market(s)

High end customers with disposable income, who also appreciate quality and unique furniture & design

Number of Pages Required

5+ page

Colors
0255a3
f37122

Requirements
Must have
• Room Planer: I will be using this tool http://qtstudio.velbarnix.com/room-planner.inc
• Live Chat
• Will be offering 3d renderings for spaces as well as Virtual Reality
• The image I loaded that looks like copper, I would like to have that as a color on the site with the texture: so the colors are Blue and copper. Would like the site to be user friendly and interactive
• http://qtstudio.velbarnix.com/ (this is the current site in development, so we will be offering Design your own, Trends, inspiration, etc...
• I have included a headshot to use for now about me. or about us.
• I also included several actual project installation (residential and commercial) as well as a variety of my furniture items
• I have Included an old Bio and some articles I would like to show case in a Press Area
• I would also like to include a section for Events (Giving back )I do a lot of charity events 1-2 a year and would like to showcase that as well
• *Please make the store (ecommerce prominent )

```html
<!DOCTYPE html>
<html lang="en">
<head>
<meta charset="utf-8">
<title>Lori Vex Studio — Interior Design &amp; Furniture</title>
<link rel="stylesheet" href="https://fonts.googleapis.com/css2?family=Playfair+Display:wght@400;700&family=Open+Sans:wght@400;600;700&display=swap">
<style>
:root{
  --orange:#f37122;
  --ink:#2b2b2b;
  --text:#555555;
  --muted:#8a8a8a;
  --paper:#ffffff;
  --mist:#f2f2f2;
  --mist-dark:#e6e6e6;
  --wine:#3a1414;
}
*{margin:0;padding:0;box-sizing:border-box}
html,body{width:1200px;height:3820px;overflow:hidden}
body{position:relative;background:var(--paper);font-family:"Open Sans",Arial,sans-serif;color:var(--text)}
.abs{position:absolute}
.serif{font-family:"Playfair Display",Georgia,serif}
.btn{position:absolute;display:inline-block;background:var(--orange);color:#fff;font:600 10px/28px "Open Sans",Arial,sans-serif;letter-spacing:1px;text-align:center;width:96px;height:28px}
.btn.light{background:#fff;color:var(--ink)}
.section-title{font-family:"Playfair Display",Georgia,serif;font-weight:400;font-size:36px;line-height:1.15;color:var(--ink)}
.copy{font-size:12px;line-height:20px;color:var(--text)}

/* backdrop shapes */
.backdrop{position:absolute;left:0;top:0;width:1200px;height:3820px}

/* hero */
.hero{left:0;top:0;width:1200px;height:600px;background:linear-gradient(135deg,#3b3836 0%,#6d6661 35%,#bdb6ad 60%,#5a534d 100%)}
.hero-shade{left:0;top:0;width:1200px;height:600px;background:linear-gradient(180deg,rgba(0,0,0,.35),rgba(0,0,0,.05) 40%,rgba(0,0,0,.3))}
.brand{left:60px;top:14px;width:150px;height:120px;text-align:center;color:#fff}
.brand-mark{display:block;width:44px;height:44px;border:0;background:#fff;margin:6px auto 8px}
.brand-name{font-family:"Playfair Display",Georgia,serif;font-size:18px;letter-spacing:3px;color:#fff;line-height:1.2}
.nav{left:512px;top:58px;display:flex;gap:6px}
.nav a{font-size:12px;color:#fff;text-decoration:none;padding:0 14px;line-height:30px}
.nav a.active{background:var(--orange)}
.nav-dot{left:1064px;top:8px;width:22px;height:22px;border-radius:50%;background:var(--orange)}
.hero-title{left:408px;top:385px;width:700px;font-family:"Playfair Display",Georgia,serif;font-weight:700;font-size:40px;line-height:56px;color:#fff}

/* about */
.about-photo{left:228px;top:700px;width:228px;height:228px;background:linear-gradient(160deg,#d9d4cf,#8e8680)}
.about-title{left:524px;top:690px}
.about-copy{left:524px;top:746px;width:560px}

/* services */
.services-title{left:228px;top:1026px}
.service-list{left:228px;top:1084px;list-style:none}
.service-list li{font-size:12px;line-height:22px;color:var(--text);padding-left:12px;position:relative}
.service-list li:before{content:"";position:absolute;left:0;top:10px;width:4px;height:4px;background:var(--orange);border-radius:50%}

.commercial-img{left:320px;top:1152px;width:480px;height:500px;background:linear-gradient(135deg,#c9c2b4,#7d8a7a 50%,#3f4a4a);clip-path:polygon(0 50%,22% 0,100% 0,100% 100%,22% 100%)}
.commercial-panel{left:760px;top:1152px;width:440px;height:500px;background:var(--orange)}
.panel-title{font-family:"Playfair Display",Georgia,serif;font-size:40px;line-height:48px;color:#fff;font-weight:400}
.panel-copy{font-size:12px;line-height:18px;color:#fff}

.residential-img{left:440px;top:1688px;width:408px;height:504px;background:linear-gradient(135deg,#e9dcc8,#8a6f55 50%,#3a2c22);clip-path:polygon(0 0,80% 0,100% 50%,80% 100%,0 100%)}

/* products */
.products-bg{left:0;top:2240px;width:1200px;height:640px;background:linear-gradient(180deg,#f7f7f7,#e4e2df 60%,#d6d3cf)}
.products-title{left:228px;top:2272px}
.products-copy{left:228px;top:2380px;width:236px}
.card{position:absolute;width:228px;height:260px;background:#fff;box-shadow:0 1px 3px rgba(0,0,0,.12)}
.card-img{position:absolute;left:14px;top:14px;width:200px;height:170px}
.card-title{position:absolute;left:16px;top:196px;font-family:"Playfair Display",Georgia,serif;font-size:17px;font-weight:700}
.card-title.hot{color:var(--orange)}
.card-title.cool{color:var(--ink)}
.card-note{position:absolute;left:16px;top:224px;font-size:10px;color:var(--muted)}

/* testimonials */
.testi-title{left:0;top:2972px;width:1200px;text-align:center}
.testi{position:absolute;top:3060px;width:240px}
.avatar{position:absolute;left:0;top:0;width:44px;height:44px;border-radius:50%;background:linear-gradient(135deg,#c7a89a,#6b4d45)}
.testi p{margin-left:58px;font-size:11px;line-height:16px;color:var(--text)}
.testi .who{margin-left:58px;margin-top:4px;font-size:11px;font-weight:700;color:var(--orange)}
.dots{left:0;top:3190px;width:1200px;display:flex;justify-content:center;gap:10px}
.dots span{width:8px;height:8px;border-radius:50%;background:#d0d0d0}
.dots span.on{background:var(--orange)}

/* contact */
.contact{left:0;top:3288px;width:1200px;height:440px;background:linear-gradient(135deg,#2a0f0f,#5a1e1c 45%,#3a1414 70%,#1d0a0a)}
.contact-title{left:0;top:3380px;width:1200px;text-align:center;font-family:"Playfair Display",Georgia,serif;font-size:40px;color:#fff}
.contact-sub{left:0;top:3440px;width:1200px;text-align:center;font-size:12px;color:#e8dcdc}
.field{position:absolute;height:34px;border-bottom:1px solid rgba(255,255,255,.55);font-size:11px;color:#eee;line-height:34px}
.send{left:552px;top:3612px}

/* footer */
.foot-nav{left:0;top:3756px;width:1200px;display:flex;justify-content:center;gap:22px}
.foot-nav a{font-size:11px;color:var(--text);text-decoration:none}
.copyright{left:0;top:3786px;width:1200px;text-align:center;font-size:10px;color:var(--muted)}
</style>
</head>
<body>

<svg class="backdrop" viewBox="0 0 1200 3820" aria-hidden="true">
  <polygon points="0,600 520,600 120,1150 0,1150" fill="#f1f1f1"/>
  <polygon points="0,1000 560,1000 300,1680 0,1680" fill="#f4f4f4"/>
  <polygon points="700,1000 1200,1000 1200,1150 820,1150" fill="#f6f6f6"/>
  <polygon points="480,1652 1200,1652 1200,2240 760,2240" fill="#f3f3f3"/>
  <polygon points="0,2192 440,2192 240,2240 0,2240" fill="#f3f3f3"/>
  <polygon points="480,1688 0,1688 0,2192 480,2192 560,1940" fill="#f37122"/>
</svg>

<!-- hero -->
<div class="abs hero" role="img" aria-label="Photograph of a styled bedroom with patterned bedding and table lamps"></div>
<div class="abs hero-shade"></div>
<div class="abs brand">
  <span class="brand-mark"></span>
  <div class="brand-name">LORI VEX<br>STUDIO</div>
</div>
<nav class="abs nav">
  <a class="active" href="#">Home</a>
  <a href="#">About Us</a>
  <a href="#">Our Services</a>
  <a href="#">Shop</a>
  <a href="#">Blog</a>
  <a href="#">Contact Us</a>
</nav>
<div class="abs nav-dot"></div>
<h1 class="abs hero-title">Lorem ipsum dolor sit amet consecteturadipiscing elit</h1>

<!-- about -->
<div class="abs about-photo" role="img" aria-label="Portrait photograph of the studio's designer"></div>
<h2 class="abs section-title about-title">About Us</h2>
<p class="abs copy about-copy">Lorem ipsum dolor sit amet, consectetur adipiscing elit. Sed do eiusmod tempor incididunt ut labore et dolore magna aliqua. Ut enim ad minim veniam, quis nostrud exercitation ullamco laboris nisi ut aliquip ex ea commodo consequat. Duis aute irure dolor in reprehenderit in voluptate velit esse cillum dolore eu fugiat nulla pariatur. Excepteur sint occaecat cupidatat non proident, sunt in culpa qui officia deserunt mollit anim id est laborum.</p>
<a class="btn" href="#" style="left:524px;top:900px">LEARN MORE</a>

<!-- services -->
<h2 class="abs section-title services-title">Our Services</h2>
<ul class="abs service-list">
  <li>Custom Designed Furniture for Commercial Interiors</li>
  <li>Space Planning</li>
  <li>Fabric Selections</li>
  <li>Lighting Direction</li>
  <li>Accessories and Décor Styling</li>
</ul>
<a class="btn" href="#" style="left:228px;top:1236px">VIEW ALL</a>

<div class="abs commercial-img" role="img" aria-label="Photograph of a colourful commercial lounge interior"></div>
<div class="abs commercial-panel"></div>
<h3 class="abs panel-title" style="left:764px;top:1280px">Commercial<br>Design</h3>
<p class="abs panel-copy" style="left:764px;top:1390px;width:230px">Lorem ipsum dolor sit amet, consectetur adipiscing elit, sed do eiusmod tempor incididunt ut labore et dolore.</p>
<a class="btn light" href="#" style="left:764px;top:1476px">VIEW ALL</a>

<div class="abs residential-img" role="img" aria-label="Photograph of a residential living room with a chandelier"></div>
<svg class="abs" style="left:0;top:1688px" width="560" height="504" viewBox="0 0 560 504" aria-hidden="true"><polygon points="0,0 480,0 560,252 480,504 0,504" fill="#f37122"/></svg>
<h3 class="abs panel-title" style="left:228px;top:1820px">Residential<br>Design</h3>
<p class="abs panel-copy" style="left:228px;top:1926px;width:230px">Lorem ipsum dolor sit amet, consectetur adipiscing elit, sed do eiusmod tempor incididunt ut labore et dolore.</p>
<a class="btn light" href="#" style="left:228px;top:2012px">VIEW ALL</a>

<!-- products -->
<div class="abs products-bg" role="img" aria-label="Faded photograph of a furnished living space"></div>
<h2 class="abs section-title products-title">Our<br>Products</h2>
<p class="abs copy products-copy">Lorem ipsum dolor sit amet, consectetur adipiscing elit, sed do eiusmod tempor incididunt ut labore et dolore magna aliqua. Ut enim ad minim veniam, quis nostrud exercitation ullamco laboris nisi ut aliquip ex ea commodo consequat. Duis aute irure dolor in reprehenderit.</p>
<a class="btn" href="#" style="left:228px;top:2532px">VIEW ALL</a>

<div class="card" style="left:484px;top:2296px">
  <div class="card-img" role="img" aria-label="Product photograph of an upholstered armchair" style="background:linear-gradient(135deg,#eeeae4,#b7aa98)"></div>
  <div class="card-title hot">Lorem Ipsum</div>
</div>
<div class="card" style="left:732px;top:2296px">
  <div class="card-img" role="img" aria-label="Product photograph of a cream cushion" style="background:linear-gradient(135deg,#f1ede5,#c8bca7)"></div>
  <div class="card-title hot">Lorem Ipsum</div>
</div>
<div class="card" style="left:484px;top:2568px">
  <div class="card-img" role="img" aria-label="Product photograph of a blue chaise lounge" style="background:linear-gradient(135deg,#e9eef3,#2e5fa0)"></div>
  <div class="card-title cool">Lorem Ipsum</div>
</div>
<div class="card" style="left:732px;top:2568px">
  <div class="card-img" role="img" aria-label="Product photograph of a pair of wooden stools" style="background:linear-gradient(135deg,#efeae3,#7d6a55)"></div>
  <div class="card-title cool">Lorem Ipsum</div>
</div>

<!-- testimonials -->
<h2 class="abs section-title testi-title">Client Testimonials</h2>
<div class="testi" style="left:228px">
  <div class="avatar" role="img" aria-label="Client portrait photograph"></div>
  <p>Lorem ipsum dolor sit amet, consectetur adipiscing elit, sed do eiusmod tempor incididunt ut labore.</p>
  <div class="who">Jane Doe</div>
</div>
<div class="testi" style="left:480px">
  <div class="avatar" role="img" aria-label="Client portrait photograph"></div>
  <p>Lorem ipsum dolor sit amet, consectetur adipiscing elit, sed do eiusmod tempor incididunt ut labore.</p>
  <div class="who">Jane Doe</div>
</div>
<div class="testi" style="left:732px">
  <div class="avatar" role="img" aria-label="Client portrait photograph"></div>
  <p>Lorem ipsum dolor sit amet, consectetur adipiscing elit, sed do eiusmod tempor incididunt ut labore.</p>
  <div class="who">Jane Doe</div>
</div>
<div class="abs dots"><span></span><span></span><span class="on"></span></div>

<!-- contact -->
<div class="abs contact" role="img" aria-label="Photograph of a dark red lounge with tufted seating"></div>
<h2 class="abs contact-title">Get In Touch</h2>
<p class="abs contact-sub">Lorem ipsum dolor sit amet, consectetur adipiscing elit, sed do eiusmod tempor incididunt.</p>
<div class="field" style="left:320px;top:3496px;width:170px">Your Name</div>
<div class="field" style="left:510px;top:3496px;width:180px">Your Email</div>
<div class="field" style="left:710px;top:3496px;width:170px">Your Phone</div>
<div class="field" style="left:320px;top:3548px;width:560px">Your Message</div>
<a class="btn send" href="#">SEND</a>

<!-- footer -->
<nav class="abs foot-nav">
  <a href="#">Home</a><a href="#">About Us</a><a href="#">Our Services</a><a href="#">Shop</a><a href="#">Blog</a><a href="#">Contact Us</a>
</nav>
<p class="abs copyright">© Copyright 2016 Lori Vex Studio. All Rights Reserved.</p>

</body>
</html>
```